New Business Card Design Project

Use the flyer uploaded and website www.brightoakbuilders.com for inspiration.
List Our Services on Backside of business cards
Marcus Delling
Harborline Builders Inc.
Licensed General Contractors
858-471-6093

Contact Information for Business Card

Use the flyer uploaded and website www.brightoakbuilders.com for inspiration. List Our Services on Backside of business cards Marcus Delling Harborline Builders Inc. Licensed General Contractors 858-471-6093

```html
<!DOCTYPE html>
<html lang="en">
<head>
<meta charset="utf-8">
<title>Harborline Builders – Business Card</title>
<link rel="stylesheet" href="https://fonts.googleapis.com/css2?family=Cinzel:wght@400&family=Montserrat:wght@400;500;700&display=swap">
<style>
  :root {
    --backdrop: #3b3532;
    --card-black: #1d1d1d;
    --card-white: #ffffff;
    --ink-dark: #1a1a1a;
    --ink-light: #f2f2f2;
    --ink-muted: #cfcfcf;
    --rule: #444444;
  }
  * { box-sizing: border-box; margin: 0; padding: 0; }
  html, body {
    width: 1200px; height: 786px; overflow: hidden;
    background: var(--backdrop);
    font-family: "Montserrat", sans-serif;
  }
  .canvas {
    position: relative; width: 1200px; height: 786px;
    display: flex; align-items: center; justify-content: center; gap: 40px;
  }
  .card {
    position: relative; width: 540px; height: 309px;
    box-shadow: 0 14px 30px rgba(0,0,0,.45);
    overflow: hidden;
  }

  /* Front */
  .card-front { background: var(--card-white); }
  .front-band {
    height: 158px; background: var(--card-black);
    display: flex; align-items: center; justify-content: center;
  }
  .brand-name {
    font-family: "Cinzel", serif; font-weight: 400;
    color: var(--ink-light); font-size: 27px; letter-spacing: 1px;
    display: flex; align-items: center; gap: 12px;
  }
  .brand-mark {
    width: 12px; height: 12px; border-radius: 50%;
    background: var(--ink-light);
  }
  .front-details {
    display: flex; justify-content: center; align-items: center;
    margin-top: 22px; gap: 18px;
  }
  .person { text-align: right; }
  .person-name { font-weight: 700; font-size: 21px; color: var(--ink-dark); }
  .person-title { font-size: 13px; color: var(--ink-dark); margin-top: 2px; }
  .divider { width: 1px; height: 72px; background: var(--ink-dark); }
  .contact-list { list-style: none; }
  .contact-list li {
    display: flex; align-items: center; gap: 10px;
    font-size: 13px; color: var(--ink-dark); line-height: 24px;
  }
  .contact-list svg { width: 13px; height: 13px; fill: var(--ink-dark); }
  .license {
    position: absolute; bottom: 20px; left: 0; right: 0;
    text-align: center; font-size: 13px; color: var(--ink-dark);
  }

  /* Back */
  .card-back { background: var(--card-black); }
  .back-content { position: absolute; left: 270px; top: 34px; right: 20px; }
  .back-content .brand-name { font-size: 22px; justify-content: flex-start; }
  .services-title {
    font-weight: 700; font-size: 14px; color: var(--ink-light);
    margin: 22px 0 6px 0;
  }
  .services-list { list-style: none; }
  .services-list li {
    font-size: 11.5px; color: var(--ink-muted); line-height: 19px;
    padding-left: 14px; position: relative;
  }
  .services-list li::before {
    content: ""; position: absolute; left: 2px; top: 8px;
    width: 4px; height: 4px; border-radius: 50%; background: var(--ink-muted);
  }
</style>
</head>
<body>
<main class="canvas">

  <section class="card card-front" aria-label="Business card front">
    <div class="front-band">
      <div class="brand-name"><span class="brand-mark"></span>Harborline Builders</div>
    </div>
    <div class="front-details">
      <div class="person">
        <p class="person-name">Marcus Delling</p>
        <p class="person-title">Managing Director</p>
      </div>
      <span class="divider"></span>
      <ul class="contact-list">
        <li><svg viewBox="0 0 16 16"><path d="M3.6 1.5l2.3 2.6-1.3 1.9c.9 2 2.4 3.5 4.4 4.4l1.9-1.3 2.6 2.3-1.2 2.2C7 15.2.8 9 1.4 2.7z"/></svg>858-471-6093</li>
        <li><svg viewBox="0 0 16 16"><path d="M1 3h14v10H1z M1.5 3.5L8 9l6.5-5.5" fill="none" stroke="#1a1a1a" stroke-width="1.4"/><path d="M1 3h14L8 8.5z"/></svg>info@brightoakbuilders.com</li>
        <li><svg viewBox="0 0 16 16"><circle cx="8" cy="8" r="7"/><path d="M1 8h14M8 1c-3 3-3 11 0 14M8 1c3 3 3 11 0 14" fill="none" stroke="#fff" stroke-width="1"/></svg>www.brightoakbuilders.com</li>
      </ul>
    </div>
    <p class="license">CSLB Licensed No. #1048215</p>
  </section>

  <section class="card card-back" aria-label="Business card back">
    <div class="back-content">
      <div class="brand-name"><span class="brand-mark"></span>Harborline Builders</div>
      <p class="services-title">Our Services</p>
      <ul class="services-list">
        <li>Remodel: Kitchen &amp; Bath</li>
        <li>Painting: Interior &amp; Exterior</li>
        <li>Flooring: Carpet, Vinyl, Wood</li>
        <li>Window: Door Replacement</li>
        <li>Plumbing: Repair &amp; Upgrades</li>
        <li>Energy Efficient Upgrades</li>
        <li>Deck &amp; Patio construction</li>
        <li>Water &amp; Mold Damage</li>
        <li>Garage Renovation</li>
      </ul>
    </div>
  </section>

</main>
</body>
</html>
```